Healthcare website

We want to replace our website using joomla as the CMS. We want it to be device agnostic (gantry etc). Our business is health care our clients are people with high level spinal cord injuries ( quadriplegia / tetraplegia etc ). The site is a marketing tool primarily to potential clients and a portal for existing staff to access forms etc. It will showcase our key staff and our capability. It will also be where any new recruits apply to work with us. It must allow us to integrate our social media initiatives also. The final design must convey sophistication, high quality care and be warm and welcoming.

current web site is www.tendralwick.com.au
Updates

I have made small change to the brief in that i have removed the prefered color and indicated it would be nice to see some images that symbolize change / transformation like butterflies etc. thank you

Target Market(s)

Our business is health care our clients are people with high level spinal cord injuries ( quadriplegia / tetraplegia etc ).

Industry/Entity Type

Marketing

Colors

Designer to choose colors to be used in the design.

Requirements
Must have
• The site is a marketing tool primarily to potential clients and a portal for existing staff to access forms etc. It will showcase our key staff and our capability. It will also be where any new recruits apply to work with us. It must allow us to integrate our social media initiatives also. The final design must convey sophistication, high quality care and be warm and welcoming.
Nice to have
• Would be nice to incorporate images that symbolize change and new transformations - butterflies etc.

```html
<!DOCTYPE html>
<html lang="en">
<head>
<meta charset="utf-8">
<title>Marlowe Homecare</title>
<link href="https://fonts.googleapis.com/css2?family=Open+Sans:wght@400;600;700&display=swap" rel="stylesheet">
<style>
:root{
  --blue:#1f5fa8;--blue-dark:#174c8a;--blue-band:#2a6bb3;--sky:#2ea3dc;
  --grey-nav:#e6e8ea;--ink:#333;--muted:#777;--footer:#2b2f33;--footer-bottom:#1f2225;--white:#fff;
}
*{box-sizing:border-box;margin:0;padding:0}
html,body{width:716px;height:1200px;overflow:hidden;background:#f4f5f6}
body{font-family:"Open Sans",Arial,sans-serif;color:var(--ink);font-size:8px;line-height:1.45}
.page{width:716px;height:1200px;position:relative;background:var(--white)}
.header{height:82px;position:relative}
.brand{position:absolute;left:28px;top:24px;display:flex;align-items:center;gap:8px;color:var(--blue);font-weight:700;font-size:22px}
.brand-mark{width:26px;height:26px;border-radius:50%;background:var(--sky)}
.portal{position:absolute;right:72px;top:52px;display:flex;gap:6px}
.portal a{background:var(--sky);color:#fff;font-size:7px;padding:4px 8px;text-decoration:none;border-radius:2px}
.nav{position:absolute;left:72px;top:90px;width:572px;height:24px;background:var(--grey-nav);display:flex;padding-left:14px;box-shadow:0 2px 3px rgba(0,0,0,.12)}
.nav a{font-size:7.5px;color:#555;text-decoration:none;padding:0 14px;line-height:24px;font-weight:600}
.nav a.active{background:var(--blue);color:#fff}
.hero{position:absolute;left:72px;top:120px;width:572px;height:242px;background:linear-gradient(135deg,#c7d3df,#8aa0b6 55%,#5c6f83)}
.hero-caption{position:absolute;left:0;bottom:14px;background:rgba(31,95,168,.85);color:#fff;font-size:15px;font-weight:700;padding:5px 14px 5px 20px}
.slider-arrows{position:absolute;left:72px;top:368px;display:flex;gap:2px}
.slider-arrows span{width:16px;height:12px;background:var(--blue-dark);display:flex;align-items:center;justify-content:center}
.band{position:absolute;left:0;top:384px;width:716px;height:308px;background:var(--blue-band);color:#fff}
.welcome{position:absolute;left:72px;top:14px;width:280px}
.band h2{font-size:17px;font-weight:600;margin-bottom:8px}
.welcome-photo{width:280px;height:96px;background:linear-gradient(120deg,#4a7fc0,#7ea6d6 50%,#2c5c98);border:3px solid #fff}
.welcome p{font-size:6.5px;margin-top:8px;opacity:.95}
.btn{display:inline-block;background:var(--white);color:var(--blue);font-size:7px;padding:6px 14px;border-radius:3px;margin-top:10px;font-weight:600}
.news{position:absolute;left:382px;top:14px;width:262px}
.news .intro{font-size:6.5px;margin-bottom:8px}
.news-item{display:flex;gap:8px;padding:6px 0;border-top:1px solid rgba(255,255,255,.25);height:49px}
.news-item .thumb{width:36px;height:36px;flex:none;background:linear-gradient(135deg,#9fb9d6,#5d84b2)}
.news-item p{font-size:6.5px}
.team{position:absolute;left:72px;top:714px;width:572px;text-align:center}
.team h3{color:var(--blue);font-size:12px;font-weight:600;margin-bottom:6px}
.team hr{border:0;border-top:1px solid #ddd;margin-bottom:12px}
.members{display:flex;justify-content:space-between;padding:0 18px}
.member{width:70px}
.member .photo{width:62px;height:62px;margin:0 auto 6px;background:linear-gradient(160deg,#d8cfc6,#a8988a);border:2px solid #fff;box-shadow:0 1px 3px rgba(0,0,0,.25)}
.member b{display:block;font-size:6.5px;color:var(--blue)}
.member span{font-size:6px;color:var(--muted)}
.join{position:absolute;left:140px;top:882px;width:436px;height:96px;border:1px solid #d6dbe0;text-align:center;padding-top:10px}
.join h3{color:var(--blue);font-size:12px;font-weight:600}
.join p{font-size:6.5px;color:var(--muted);margin-top:4px}
.join .btn{background:var(--blue);color:#fff;margin-top:10px}
.footer{position:absolute;left:0;top:1004px;width:716px;height:178px;background:var(--footer);color:#ccc}
.footer h4{color:#fff;font-size:9px;margin-bottom:6px}
.fcol{position:absolute;top:16px;font-size:6.5px}
.fcol.licensed{left:72px;width:160px}
.fcol.contact{left:290px;width:170px}
.fcol.location{left:500px;width:144px}
.fcol .row{display:flex;gap:5px;align-items:center;margin-bottom:5px}
.map{width:144px;height:96px;background:linear-gradient(135deg,#e7e3d8,#cfd8c8);border:2px solid #fff}
.bottom-bar{position:absolute;left:0;top:1182px;width:716px;height:18px;background:var(--footer-bottom);color:#999;font-size:6px;line-height:18px}
.bottom-bar .copy{position:absolute;left:72px}
.bottom-bar .links{position:absolute;right:72px}
</style>
</head>
<body>
<div class="page">
  <header class="header">
    <div class="brand"><span class="brand-mark"></span>Marlowe Homecare</div>
    <div class="portal"><a href="#">STAFF LOGIN</a><a href="#">CLIENT LOGIN</a></div>
  </header>
  <nav class="nav">
    <a class="active" href="#">HOME</a><a href="#">ABOUT US</a><a href="#">OUR SERVICES</a><a href="#">RESOURCES</a><a href="#">NEWS &amp; EVENTS</a><a href="#">CONTACT US</a>
  </nav>
  <section class="hero" role="img" aria-label="Smiling carer in a clinic setting">
    <div class="hero-caption">TO PROVIDE THE BEST CARE</div>
  </section>
  <div class="slider-arrows">
    <span><svg width="6" height="8" viewBox="0 0 6 8"><path d="M5 0L1 4l4 4" fill="none" stroke="#fff" stroke-width="1.5"/></svg></span>
    <span><svg width="6" height="8" viewBox="0 0 6 8"><path d="M1 0l4 4-4 4" fill="none" stroke="#fff" stroke-width="1.5"/></svg></span>
  </div>
  <section class="band">
    <div class="welcome">
      <h2>Welcome</h2>
      <div class="welcome-photo" role="img" aria-label="Care team group photo with blue balloons"></div>
      <p>Marlowe Homecare has built its name on meeting the needs of each and every client. We listen to and consult with our clients, their families, case managers and the wider care community.</p>
      <p>Marlowe Homecare is a privately owned organisation providing in-home care to people with disabilities, delivered across Victoria. We commenced operation in 2002 and continue to grow.</p>
      <p>We are committed to our vision, "to provide the best care", and we are fully accountable to our clients, carers and funding organisations. We are proud to support every client we serve.</p>
      <span class="btn">Read More</span>
    </div>
    <div class="news">
      <h2>Disability News</h2>
      <p class="intro">The latest spinal cord injury news, information and resources for people living with spinal cord injury.</p>
      <div class="news-item"><div class="thumb" role="img" aria-label="News photo"></div><p><b>New methods show promise for rehabilitating paralysed patients with spinal cord injury</b></p></div>
      <div class="news-item"><div class="thumb" role="img" aria-label="News photo"></div><p><b>Stem cell advances renew hope for repair of injured nerves</b></p></div>
      <div class="news-item"><div class="thumb" role="img" aria-label="News photo"></div><p><b>Wheelchair rugby a family affair for mum and son</b></p></div>
      <div class="news-item"><div class="thumb" role="img" aria-label="News photo"></div><p><b>Attitude can play a significant role in recovery from paralysing injury</b></p></div>
    </div>
  </section>
  <section class="team">
    <h3>Our Team</h3><hr>
    <div class="members">
      <div class="member"><div class="photo" role="img" aria-label="Staff portrait"></div><b>Leo Harmon</b><span>Care Team Lead</span></div>
      <div class="member"><div class="photo" role="img" aria-label="Staff portrait"></div><b>Mara Fenwick</b><span>Care Coordinator</span></div>
      <div class="member"><div class="photo" role="img" aria-label="Staff portrait"></div><b>Sara Lindell</b><span>Nurse Manager</span></div>
      <div class="member"><div class="photo" role="img" aria-label="Staff portrait"></div><b>Dana Ortley</b><span>Client Liaison</span></div>
      <div class="member"><div class="photo" role="img" aria-label="Staff portrait"></div><b>Tessa Rowe</b><span>Rostering Officer</span></div>
    </div>
  </section>
  <section class="join">
    <h3>Join Our Team</h3>
    <p>We are always on the lookout for great people to work with our clients.</p>
    <p>If you want to be a part of our team click below to apply.</p>
    <span class="btn">Apply Now</span>
  </section>
  <footer class="footer">
    <div class="fcol licensed">
      <h4>Licensed</h4>
      <p>Marlowe Homecare is proud to be an approved provider for transport accident and workcover claims in Victoria. We hold registrations with state disability services and work closely with leading insurers.</p>
    </div>
    <div class="fcol contact">
      <h4>Contact Us</h4>
      <div class="row"><svg width="7" height="9" viewBox="0 0 7 9"><path d="M3.5 0A3.5 3.5 0 0 0 0 3.5C0 6 3.5 9 3.5 9S7 6 7 3.5A3.5 3.5 0 0 0 3.5 0z" fill="#ccc"/></svg>Suite 4, 18 Larkin Street, Fernvale VIC 3099</div>
      <div class="row"><svg width="8" height="8" viewBox="0 0 8 8"><path d="M1 0h2l1 2-1 1a5 5 0 0 0 2 2l1-1 2 1v2A1 1 0 0 1 7 8 7 7 0 0 1 0 1a1 1 0 0 1 1-1z" fill="#ccc"/></svg>Call Us: (03) 9000 1234</div>
      <div class="row"><svg width="8" height="8" viewBox="0 0 8 8"><path d="M1 0h2l1 2-1 1a5 5 0 0 0 2 2l1-1 2 1v2A1 1 0 0 1 7 8 7 7 0 0 1 0 1a1 1 0 0 1 1-1z" fill="#ccc"/></svg>Fax: (03) 9000 1235</div>
      <div class="row"><svg width="9" height="7" viewBox="0 0 9 7"><rect x=".5" y=".5" width="8" height="6" fill="none" stroke="#ccc"/><path d="M.5.5l4 3 4-3" fill="none" stroke="#ccc"/></svg>Email: hello@marlowehomecare.org</div>
    </div>
    <div class="fcol location">
      <h4>Our Location</h4>
      <div class="map" role="img" aria-label="Street map showing office location"></div>
    </div>
  </footer>
  <div class="bottom-bar"><span class="copy">Copyright © 2014 Marlowe Homecare Pty Ltd. All Rights Reserved.</span><span class="links">Privacy | Terms of Service</span></div>
</div>
</body>
</html>
```